Velmarotix - world unique technology for better life - please let them know who am i at first sight

We need a new business card for company which is a provider of unique crystal based technology suitable for all living being. For more information and final design you can use our brochure (our colours are black and blue from brochure).
We use Verdana font

Industry/Entity Type

Business

Contact Information for Business Card

regular dimension

Font styles to use
Other font styles liked:
• Verdana

Requirements
Must have
• Logo
• name
• function/position
• phone
• mobile
• e-mail
• adress
Nice to have
• inovative design (technology directed)

```html
<!DOCTYPE html>
<html lang="en">
<head>
<meta charset="utf-8">
<title>Velmarotix business card</title>
<link rel="stylesheet" href="https://fonts.googleapis.com/css2?family=Open+Sans:wght@300;400;700&display=swap">
<style>
:root{
  --stage:#6abf3f;
  --card:#0b0b0b;
  --blue:#2f9fd8;
  --white:#f2f2f2;
}
*{margin:0;padding:0;box-sizing:border-box}
html,body{width:1200px;height:381px;overflow:hidden;background:var(--stage)}
body{position:relative;font-family:Verdana,"Open Sans",sans-serif;color:var(--white)}
.card{position:absolute;top:37px;width:554px;height:319px;background:var(--card);overflow:hidden}
.card--front{left:30px}
.card--back{left:618px}
.pattern{position:absolute;border-radius:50%;
  background:radial-gradient(circle,rgba(58,63,68,.15) 0%,rgba(58,63,68,.9) 55%,rgba(58,63,68,.35) 72%,rgba(58,63,68,0) 74%)}
.card--front .pattern{left:380px;top:5px;width:300px;height:300px}
.card--back .pattern{left:-150px;top:-25px;width:290px;height:290px}
.brand{position:absolute;display:flex;align-items:center;gap:18px;white-space:nowrap}
.brand__dot{flex:none;width:86px;height:86px;border-radius:50%;background:var(--blue)}
.brand__name{font-family:"Open Sans",Verdana,sans-serif;font-weight:300;color:var(--blue);letter-spacing:1px;line-height:1}
.card--front .brand{left:24px;top:32px}
.card--front .brand__name{font-size:40px}
.card--back .brand{right:78px;top:120px}
.card--back .brand__name{font-size:46px}
.person{position:absolute;left:24px;top:148px;height:22px;line-height:22px;font-size:13.5px;white-space:nowrap}
.person__name{font-weight:700;color:var(--blue);font-size:17px}
.contacts{position:absolute;left:24px;top:189px;list-style:none;font-size:12.5px}
.contacts li{display:flex;align-items:center;gap:8px;height:22px;line-height:22px;white-space:nowrap}
.contacts svg{flex:none;width:12px;height:12px;fill:var(--blue)}
.address{position:absolute;left:24px;top:287px;height:18px;line-height:18px;font-size:12.5px;white-space:nowrap}
.website{position:absolute;left:212px;top:213px;width:300px;height:20px;line-height:20px;text-align:center;font-weight:700;font-size:14px;letter-spacing:2px;white-space:nowrap}
</style>
</head>
<body>
<section class="card card--front">
  <div class="pattern" role="img" aria-label="Faint crystal lattice decoration"></div>
  <div class="brand"><span class="brand__dot"></span><span class="brand__name">VELMAROTIX</span></div>
  <p class="person"><span class="person__name">Mira Stolten,</span> Founder and CEO</p>
  <ul class="contacts">
    <li><svg viewBox="0 0 16 16"><path d="M3 1l3 3-2 2c1 2 3 4 6 6l2-2 3 3-2 3C7 16 0 9 0 3z"/></svg>012-555-0147</li>
    <li><svg viewBox="0 0 16 16"><path d="M4 0h8v16H4zM5 2v10h6V2z" fill-rule="evenodd"/></svg>012-555-0147</li>
    <li><svg viewBox="0 0 16 16"><path d="M0 3h16v10H0zM1 4l7 5 7-5z" fill-rule="evenodd"/></svg>info@velmarotix.com</li>
    <li><svg viewBox="0 0 16 16"><circle cx="8" cy="8" r="7" fill="none" stroke="#2f9fd8" stroke-width="1.5"/><path d="M1 8h14M8 1c-4 4-4 10 0 14M8 1c4 4 4 10 0 14" fill="none" stroke="#2f9fd8" stroke-width="1.2"/></svg>www.velmarotix.cu</li>
  </ul>
  <p class="address">Street Name, City Name, Zipcode-01234</p>
</section>
<section class="card card--back">
  <div class="pattern" role="img" aria-label="Faint crystal lattice decoration"></div>
  <div class="brand"><span class="brand__name">VELMAROTIX</span></div>
  <p class="website">www.velmarotix.cu</p>
</section>
</body>
</html>
```